Corvane Freight Company Business Card Design

We are a company that delivers natural saltwater (from the ocean) to aquarium companies, restaurants and home marine tanks. I would like a new business card to suit.

Must include Name, company name, abn, contact number and website as well as logo (see attached).

Looking for a design that stands out, has a clean but unique appearance.

Double and single sided entries welcome

Business

• Logo

```html
<!DOCTYPE html>
<html lang="en">
<head>
<meta charset="utf-8">
<title>Corvane Freight Company – Business Card</title>
<link rel="stylesheet" href="https://fonts.googleapis.com/css2?family=Source+Sans+3:wght@400;600;700&display=swap">
<style>
  :root {
    --backdrop: #141414;
    --sky: #55c9f2;
    --ocean: #0b5dab;
    --white: #ffffff;
    --card-edge: #9fb9d6;
  }
  * { box-sizing: border-box; margin: 0; padding: 0; }
  html, body {
    width: 1200px; height: 420px; overflow: hidden;
    background: var(--backdrop);
    font-family: "Source Sans 3", "Myriad Pro", sans-serif;
  }
  .stage { position: relative; width: 1200px; height: 420px; }
  .card {
    position: absolute; top: 64px;
    width: 518px; height: 295px;
    border-radius: 18px; overflow: hidden;
  }
  .card--front { left: 69px; background: var(--white); }
  .card--back { left: 620px; background: var(--ocean); border: 1px solid var(--card-edge); }

  .front__header {
    height: 45px; background: var(--sky);
    color: var(--white); text-align: center;
    font-size: 18px; line-height: 45px; letter-spacing: 0.6px;
  }
  .front__header .person-name { font-weight: 700; }
  .front__header .person-title { font-weight: 400; font-size: 16px; }

  .front__brand {
    height: 173px; display: flex; align-items: center; justify-content: center;
  }
  .brand-name {
    text-align: center; font-weight: 400; line-height: 1;
    color: var(--sky); font-size: 40px;
  }
  .card--back .brand-name { color: var(--white); font-size: 50px; }

  .front__footer {
    height: 77px; background: var(--ocean); color: var(--white);
    text-align: center; font-size: 13px; line-height: 20px; padding-top: 4px;
  }
  .contact-row { display: flex; justify-content: center; gap: 22px; }
  .contact-item { display: inline-flex; align-items: center; gap: 6px; }
  .contact-item svg { width: 11px; height: 11px; }

  .back__brand {
    height: 100%; display: flex; align-items: center; justify-content: center;
  }
</style>
</head>
<body>
<main class="stage">
  <section class="card card--front" aria-label="Card front">
    <header class="front__header">
      <span class="person-name">Your Name,</span> <span class="person-title">Title</span>
    </header>
    <div class="front__brand">
      <p class="brand-name">Corvane Freight<br>Company</p>
    </div>
    <footer class="front__footer">
      <div class="contact-row">
        <span class="contact-item">
          <svg viewBox="0 0 12 12" aria-hidden="true"><path fill="#fff" d="M2.5 0.8 L4.3 2.9 L3.4 4.2 C4 5.7 5.3 7.1 6.9 7.9 L8.2 7 L10.6 8.6 L9.6 10.8 C5.2 10.5 1.3 6.6 0.9 2.1 Z"/></svg>
          123-456-7892
        </span>
        <span class="contact-item">
          <svg viewBox="0 0 12 12" aria-hidden="true"><g fill="none" stroke="#fff" stroke-width="1.1"><circle cx="6" cy="6" r="5"/><ellipse cx="6" cy="6" rx="2.2" ry="5"/><line x1="1" y1="6" x2="11" y2="6"/></g></svg>
          www.corvanefreight.com
        </span>
      </div>
      <p>Street Name, City Name ,State, Zip Code</p>
      <p>ABN: 123456789</p>
    </footer>
  </section>

  <section class="card card--back" aria-label="Card back">
    <div class="back__brand">
      <p class="brand-name">Corvane Freight<br>Company</p>
    </div>
  </section>
</main>
</body>
</html>
```